Veldmark Supplies Business Card

Professional business card that stand out to our potential customers. Front and back with clean modern design

Industry/Entity Type

Oil and gas

Contact Information for Business Card

Name, address, website , office phone and cell number

Requirements
Must have
• Editable files for each employee

```html
<!DOCTYPE html>
<html lang="en">
<head>
<meta charset="utf-8">
<title>Veldmark Supplies Business Card</title>
<link href="https://fonts.googleapis.com/css2?family=Michroma&family=Poppins:wght@400&display=swap" rel="stylesheet">
<style>
  :root {
    --stage: #2b2b2b;
    --card: #ffffff;
    --brand-red: #ff1010;
    --brand-blue: #12aacb;
    --ink: #1b1b1b;
    --rule: #8d8d8d;
    --grad-red: #ff0000;
    --grad-mid: #7a6f83;
    --grad-blue: #06b4d6;
  }
  * { box-sizing: border-box; margin: 0; padding: 0; }
  html, body { width: 1200px; height: 1108px; overflow: hidden; }
  body {
    background: var(--stage);
    display: flex;
    align-items: center;
    justify-content: center;
    gap: 70px;
    font-family: "Poppins", sans-serif;
  }
  .card {
    width: 470px;
    height: 820px;
    border-radius: 26px;
    position: relative;
    overflow: hidden;
  }
  .card-front {
    background: var(--card);
    display: flex;
    flex-direction: column;
    align-items: center;
    padding-top: 150px;
  }
  .brand {
    display: flex;
    align-items: center;
    gap: 14px;
  }
  .brand-square {
    width: 30px;
    height: 30px;
    background: var(--brand-red);
  }
  .brand-name {
    font-family: "Michroma", sans-serif;
    font-size: 25px;
    color: var(--brand-red);
    letter-spacing: 1px;
    text-transform: uppercase;
  }
  .person-name {
    margin-top: 150px;
    font-family: "Michroma", sans-serif;
    font-size: 27px;
    letter-spacing: 1px;
    text-transform: uppercase;
  }
  .person-name .first { color: var(--brand-red); }
  .person-name .last { color: var(--brand-blue); }
  .icon-row {
    margin-top: 22px;
    display: flex;
    align-items: center;
    gap: 8px;
    width: 330px;
  }
  .icon-row .rule { flex: 1; height: 1px; background: var(--rule); }
  .icon-box {
    width: 40px;
    height: 40px;
    border-radius: 9px;
    background: var(--brand-red);
    display: flex;
    align-items: center;
    justify-content: center;
  }
  .contact-lines {
    margin-top: 12px;
    text-align: center;
    font-size: 24px;
    line-height: 1.3;
    color: var(--ink);
  }
  .divider {
    width: 330px;
    height: 1px;
    background: var(--rule);
    margin: 22px 0 18px;
  }
  .address {
    text-align: center;
    font-size: 22px;
    line-height: 1.35;
    color: var(--ink);
  }
  .card-back {
    background: linear-gradient(225deg, var(--grad-blue) 10%, var(--grad-mid) 48%, var(--grad-red) 90%);
  }
  .back-brand {
    position: absolute;
    left: 0;
    right: 0;
    bottom: 200px;
    text-align: center;
    font-family: "Michroma", sans-serif;
    font-size: 17px;
    color: #ffffff;
    text-transform: uppercase;
    letter-spacing: 1px;
  }
</style>
</head>
<body>
  <section class="card card-front" aria-label="Card front">
    <div class="brand">
      <span class="brand-square"></span>
      <span class="brand-name">Veldmark Supplies</span>
    </div>

    <h1 class="person-name"><span class="first">Marcus</span> <span class="last">Ellery</span></h1>

    <div class="icon-row">
      <span class="rule"></span>
      <span class="icon-box" aria-label="Office phone">
        <svg width="24" height="24" viewBox="0 0 24 24"><path d="M6.6 10.8a15 15 0 0 0 6.6 6.6l2.2-2.2a1 1 0 0 1 1-.25 11.4 11.4 0 0 0 3.6.57 1 1 0 0 1 1 1V20a1 1 0 0 1-1 1A17 17 0 0 1 3 4a1 1 0 0 1 1-1h3.5a1 1 0 0 1 1 1c0 1.25.2 2.45.57 3.57a1 1 0 0 1-.25 1z" fill="#fff"/></svg>
      </span>
      <span class="icon-box" aria-label="Mobile phone">
        <svg width="24" height="24" viewBox="0 0 24 24"><rect x="6" y="2" width="12" height="20" rx="2" fill="#fff"/><rect x="8" y="5" width="8" height="12" fill="#ff1010"/><circle cx="12" cy="19.3" r="1" fill="#ff1010"/></svg>
      </span>
      <span class="icon-box" aria-label="Website">
        <svg width="24" height="24" viewBox="0 0 24 24"><circle cx="12" cy="12" r="9" fill="none" stroke="#fff" stroke-width="2"/><ellipse cx="12" cy="12" rx="4" ry="9" fill="none" stroke="#fff" stroke-width="1.6"/><path d="M3 12h18" stroke="#fff" stroke-width="1.6"/></svg>
      </span>
      <span class="rule"></span>
    </div>

    <div class="contact-lines">
      <p>044-987 650 214</p>
      <p>044-987 650 214</p>
      <p>www.veldmarksupply.com</p>
    </div>

    <div class="divider"></div>

    <address class="address" style="font-style:normal">
      <p>17 Quarry Road, Suite 4</p>
      <p>78210, Westfield</p>
    </address>
  </section>

  <section class="card card-back" role="img" aria-label="Red to blue gradient with a repeating embossed company monogram pattern">
    <span class="back-brand">Veldmark Supplies</span>
  </section>
</body>
</html>
```